Banner ads for LP that work with same theme as below banners

Love the banner ads below. Need more with attached photos. But use the same wording, font as in below banner ads. Should be LP size 1200/627 so I can use for Pixorly and LP. Looking for great ads to use as LP ads. We do lots of ads so it will be worth your time to enter this contest you will be rewarded with a ton of work. Need several banner ads that work together. So maybe 1 of the dresses, 1 of the sweater, 1 of the leggings, 1 of the jacket

Target Market(s)

Women 24-45

Industry/Entity Type

Fashion

Requirements
Must have
• Banner ads that work for LP and Pixorly
Nice to have
• Several options to choose from
Should not have
• not sure

```html
<!DOCTYPE html>
<html lang="en">
<head>
<meta charset="UTF-8">
<title>Our Best Sweater Ever – Banner</title>
<link rel="stylesheet" href="https://fonts.googleapis.com/css2?family=Berkshire+Swash&family=Playfair+Display+SC:wght@700&family=Libre+Baskerville:wght@700&display=swap">
<style>
  :root {
    --bg-deep: #b0402a;
    --bg-mid: #d9782f;
    --bg-light: #ead98f;
    --script-red: #8a1c10;
    --headline-white: #ffffff;
    --button-line: rgba(255, 248, 235, 0.75);
    --side-word: rgba(190, 150, 60, 0.28);
    --knit-light: #c9c4d0;
    --knit-mid: #a7a3ad;
  }
  * { margin: 0; padding: 0; box-sizing: border-box; }
  html, body { width: 1200px; height: 627px; overflow: hidden; }
  .banner {
    position: relative;
    width: 1200px;
    height: 627px;
    overflow: hidden;
    background:
      radial-gradient(ellipse 70% 80% at 95% 5%, var(--bg-light) 0%, rgba(234,217,143,0) 70%),
      linear-gradient(115deg, var(--bg-deep) 0%, #c65a2c 35%, var(--bg-mid) 60%, #e2b35c 85%, var(--bg-light) 100%);
  }
  .model-photo {
    position: absolute;
    left: 30px;
    top: 40px;
    width: 450px;
    height: 587px;
    border-radius: 60px 60px 0 0;
    background: linear-gradient(100deg, var(--knit-light) 0%, var(--knit-mid) 45%, var(--knit-light) 70%, #b9b7bb 100%);
    filter: blur(1px);
  }
  .headline {
    position: absolute;
    left: 560px;
    top: 140px;
    width: 350px;
    text-align: center;
  }
  .headline__script {
    display: block;
    font-family: "Berkshire Swash", cursive;
    font-size: 52px;
    color: var(--script-red);
    letter-spacing: 4px;
    line-height: 1;
  }
  .headline__main {
    display: block;
    font-family: "Playfair Display SC", serif;
    font-weight: 700;
    font-size: 66px;
    color: var(--headline-white);
    letter-spacing: 6px;
    line-height: 1;
    margin: 14px 0 18px;
  }
  .cta {
    position: absolute;
    left: 650px;
    top: 402px;
    width: 218px;
    height: 56px;
    border: 1px solid var(--button-line);
    display: flex;
    align-items: center;
    justify-content: center;
    font-family: "Libre Baskerville", serif;
    font-weight: 700;
    font-size: 13px;
    letter-spacing: 2.5px;
    color: var(--headline-white);
  }
  .side-word {
    position: absolute;
    left: 1135px;
    top: 318px;
    transform: translate(-50%, -50%) rotate(-90deg);
    font-family: "Playfair Display SC", serif;
    font-weight: 700;
    font-size: 112px;
    letter-spacing: 12px;
    color: var(--side-word);
    white-space: nowrap;
  }
</style>
</head>
<body>
  <div class="banner">
    <div class="side-word" aria-hidden="true">SWEATER</div>
    <div class="model-photo" role="img" aria-label="Two models wearing oversized grey knit turtleneck sweaters"></div>
    <h1 class="headline">
      <span class="headline__script">Our Best</span>
      <span class="headline__main">SWEATER</span>
      <span class="headline__script">Ever!</span>
    </h1>
    <div class="cta">SHOP THE LOOK</div>
  </div>
</body>
</html>
```